Store Promo Card (already have logo!)

I need a card design (single side) for my online women’s gift shop containing a promotional code to be placed in bags for attendees at an event. I’m flexible on both shape and sizing, but perhaps a 4x6 card.
—It should contain my attached logo, my website (www.brivelhome.com), and my Instagram handle (@brivelhome) and promotion language such as “15% off your purchase with code: PELVON”.
—I think I would like my logo to be large.
—It should be clean, simple and modern in design and should use the colors from my logo.
—I would like about 3-5 product pictures depending on design.
Target Market(s)
Women ages 30 to 60
Industry/Entity Type
Retail Upscale Gift

```html
<!DOCTYPE html>
<html lang="en">
<head>
<meta charset="utf-8">
<title>Brivel Home – Promo Card</title>
<link rel="stylesheet" href="https://fonts.googleapis.com/css2?family=Abril+Fatface&family=Playfair+Display:wght@400;700&display=swap">
<style>
  :root {
    --backdrop: #ece2d5;
    --paper: #f8f5f2;
    --blush: #e8b9ae;
    --ink: #2f3130;
    --slipper-lilac: #a08cab;
    --slipper-puff: #f0dcd0;
  }
  * { box-sizing: border-box; margin: 0; padding: 0; }
  html, body {
    width: 1200px; height: 800px; overflow: hidden;
    background: var(--backdrop);
  }
  .promo-card {
    position: absolute; left: 80px; top: 120px;
    width: 1040px; height: 560px;
    background: var(--paper);
    padding: 34px;
    box-shadow: 0 6px 18px rgba(80, 60, 40, 0.18);
  }
  .card-face {
    position: relative; width: 100%; height: 100%;
    background: var(--blush);
    color: var(--ink);
  }
  .frame {
    position: absolute;
    border: 2px solid var(--ink);
  }
  .frame-label {
    position: absolute; left: 50%; bottom: 0;
    transform: translate(-50%, 55%);
    background: var(--blush);
    padding: 0 16px;
    white-space: nowrap;
  }
  .brand-name {
    position: absolute; left: 46px; top: 84px;
    width: 430px; height: 200px;
    display: flex; align-items: center; justify-content: center;
    font-family: "Playfair Display", serif;
    font-weight: 700; font-size: 58px; letter-spacing: 2px;
    white-space: nowrap;
  }
  .contact-frame { left: 72px; top: 308px; width: 430px; height: 148px; }
  .contact-url {
    font-family: "Playfair Display", serif;
    font-size: 38px; text-align: center; margin-top: 42px;
  }
  .contact-handle {
    font-family: "Playfair Display", serif;
    font-size: 32px;
    display: flex; align-items: center; gap: 14px;
  }
  .handle-mark {
    width: 22px; height: 22px;
    border: 2.5px solid var(--ink); border-radius: 50%;
  }
  .offer-frame {
    left: 530px; top: 34px; width: 402px; height: 420px;
    display: flex; flex-direction: column; align-items: center;
  }
  .offer-headline {
    font-family: "Abril Fatface", serif;
    font-weight: 400; font-size: 68px; line-height: 1; margin-top: 24px;
  }
  .product-photo {
    width: 250px; height: 176px; margin-top: 18px;
    background: linear-gradient(160deg, var(--slipper-puff) 0%, var(--slipper-puff) 45%, var(--slipper-lilac) 100%);
  }
  .offer-terms {
    font-family: "Playfair Display", serif;
    font-weight: 700; font-size: 22px; margin-top: 26px;
  }
  .offer-code {
    font-family: "Playfair Display", serif;
    font-weight: 700; font-size: 40px; letter-spacing: 1px; line-height: 1.1;
  }
</style>
</head>
<body>
  <main class="promo-card">
    <div class="card-face">
      <h1 class="brand-name">BRIVEL HOME</h1>

      <section class="frame contact-frame">
        <p class="contact-url">www.brivelhome.com</p>
        <p class="frame-label contact-handle"><span class="handle-mark"></span>@brivelhome</p>
      </section>

      <section class="frame offer-frame">
        <h2 class="offer-headline">10% OFF</h2>
        <div class="product-photo" role="img" aria-label="Product photo: lilac slippers with fluffy blush pom-poms"></div>
        <p class="offer-terms">your purchase with code:</p>
        <p class="offer-code">PELVON</p>
      </section>
    </div>
  </main>
</body>
</html>
```